Local Roofing Company Billboard Design

We need a billboard design for an 8' x 32' billboard. This billboard would need to be easily readable and stand out well.
I have uploaded a design that we like - simple, readable, and gets the point across. We do NOT want the $1000 off offer included.
We are looking for a black background with white copy so it will stand out. We want the following on the billboard:
Brindlewick Roofing logo
brindlewick-roofing.example (optional)
555.214.7730 (mandatory)
Photo is optional, depends on how it all lays out
Production file must comply with layout requirements (uploaded).
Target Market(s)
Homeowners
Font styles to use
Other font styles liked:
- match font from logo
Colors
Designer to choose colors to be used in the design.
Requirements
Must have
- Black background, white copy, logo must be large and legible. Colors used must match our logo colors.

```html
<!DOCTYPE html>
<html lang="en">
<head>
<meta charset="utf-8">
<title>Brindlewick Roofing Billboard</title>
<link href="https://fonts.googleapis.com/css2?family=Oswald:wght@700&family=Open+Sans:wght@700&family=Arvo:wght@700&display=swap" rel="stylesheet">
<style>
  :root {
    --black: #000000;
    --white: #ffffff;
    --orange: #e85a24;
    --seal: #d9d9d9;
    --stage: #e6e7ea;
  }
  * { margin: 0; padding: 0; box-sizing: border-box; }
  html, body {
    width: 1200px;
    height: 688px;
    overflow: hidden;
    background: var(--stage);
  }
  .billboard {
    position: absolute;
    left: 0;
    top: 180px;
    width: 1200px;
    height: 328px;
    overflow: hidden;
    background: var(--white);
  }
  .billboard__shapes {
    position: absolute;
    inset: 0;
    width: 100%;
    height: 100%;
  }
  .billboard__phone {
    position: absolute;
    left: 26px;
    top: 14px;
    font-family: "Oswald", "Arial Narrow", sans-serif;
    font-weight: 700;
    font-size: 104px;
    line-height: 1.2;
    letter-spacing: -2px;
    color: var(--orange);
    white-space: nowrap;
  }
  .billboard__services {
    position: absolute;
    left: 30px;
    top: 145px;
    font-family: "Open Sans", Arial, sans-serif;
    font-weight: 700;
    font-size: 23px;
    line-height: 37px;
    color: var(--white);
  }
  .billboard__brand {
    position: absolute;
    left: 592px;
    top: 210px;
    font-family: "Arvo", "Rockwell", serif;
    font-weight: 700;
    font-size: 51px;
    line-height: 1;
    color: var(--black);
    white-space: nowrap;
  }
</style>
</head>
<body>
  <main class="billboard">
    <svg class="billboard__shapes" viewBox="0 0 1188 325" preserveAspectRatio="none" aria-hidden="true">
      <polygon class="panel-dark" points="0,0 852,0 172,325 0,325" fill="var(--black)"/>
      <polygon class="accent-stripe" points="852,0 886,0 214,325 172,325" fill="var(--orange)"/>
      <polygon class="accent-corner" points="886,0 1188,0 1188,150" fill="var(--orange)"/>
      <circle class="certification-seal" cx="484" cy="222" r="58" fill="var(--seal)"/>
    </svg>

    <p class="billboard__phone">555.214.7730</p>
    <p class="billboard__services">We install all types of<br>Residential and Commercial<br>roofing across Arizona</p>
    <p class="billboard__brand">Brindlewick Roofing</p>
  </main>
</body>
</html>
```